Business Card Design

Business Card for professional consulting firm working with large financial institutions.

Target Market(s)

Executive buyers

Industry/Entity Type

Banking

Contact Information for Business Card

Mild creativity wanted. Not boring, but do elaborate artwork.

Font styles to use
Serif
Sans Serif

Colors

Designer to choose colors to be used in the design.

Requirements
Must have
• Standard business card features - company name, individual name, telephone, website, email, locations.
Nice to have
• Two colors
Should not have
• too many colors, fancy printing, cartoons.

```html
<!DOCTYPE html>
<html lang="en">
<head>
<meta charset="utf-8">
<title>k7advisory Business Card</title>
<link href="https://fonts.googleapis.com/css2?family=Lato:wght@400;700&display=swap" rel="stylesheet">
<style>
  :root {
    --backdrop: #7b7b7b;
    --card-white: #ffffff;
    --brand-blue: #062f86;
    --ink: #222222;
    --rule-grey: #bdbdbd;
  }
  * { margin: 0; padding: 0; box-sizing: border-box; }
  html, body {
    width: 1200px; height: 1200px; overflow: hidden;
    background: var(--backdrop);
    font-family: "Lato", sans-serif;
  }
  .stage { position: relative; width: 1200px; height: 1200px; }
  .card {
    position: absolute; top: 310px; height: 594px;
    box-shadow: 2px 3px 4px rgba(0,0,0,0.45);
    text-align: center;
  }
  .card--front { left: 234px; width: 364px; background: var(--card-white); color: var(--ink); }
  .card--back { left: 627px; width: 370px; background: var(--brand-blue); color: var(--card-white); }

  .wordmark {
    position: absolute; left: 0; right: 0;
    font-weight: 400; font-size: 34px; letter-spacing: 0.5px;
    display: flex; justify-content: center; align-items: center; gap: 10px;
  }
  .wordmark__dot { width: 12px; height: 12px; border-radius: 50%; background: currentColor; }
  .card--front .wordmark { top: 157px; color: var(--brand-blue); }
  .card--back .wordmark { top: 277px; color: var(--card-white); }

  .person { position: absolute; top: 312px; left: 0; right: 0; }
  .person__name { font-weight: 700; font-size: 21px; color: var(--brand-blue); letter-spacing: 0.2px; }
  .person__role { font-size: 17px; margin-top: 1px; }

  .icon-row {
    position: absolute; top: 372px; left: 87px; width: 190px;
    display: flex; align-items: center; gap: 3px;
  }
  .icon-row__rule { flex: 1; height: 1px; background: var(--ink); }
  .icon-row__badge {
    width: 24px; height: 24px; border-radius: 50%; background: var(--brand-blue);
    display: flex; align-items: center; justify-content: center;
  }
  .contact { position: absolute; top: 408px; left: 0; right: 0; font-size: 17px; line-height: 22px; }
  .divider { position: absolute; top: 489px; left: 87px; width: 190px; height: 2px; background: var(--rule-grey); }
  .address { position: absolute; top: 507px; left: 0; right: 0; font-size: 17px; line-height: 22px; }
  .card--back .web { position: absolute; top: 520px; left: 0; right: 0; font-size: 16px; }
</style>
</head>
<body>
<main class="stage">
  <section class="card card--front">
    <div class="wordmark"><span>k7advisory</span><span class="wordmark__dot"></span></div>
    <div class="person">
      <p class="person__name">JONATHAN SMITH</p>
      <p class="person__role">Managing Director</p>
    </div>
    <div class="icon-row">
      <span class="icon-row__rule"></span>
      <span class="icon-row__badge" aria-label="phone">
        <svg width="14" height="14" viewBox="0 0 14 14"><path d="M2 5 Q7 1 12 5 L11 7 L9 6 L9 5 Q7 4 5 5 L5 6 L3 7 Z M4 8 H10 L11 12 H3 Z" fill="#fff"/></svg>
      </span>
      <span class="icon-row__badge" aria-label="email">
        <svg width="14" height="14" viewBox="0 0 14 14"><rect x="2" y="3.5" width="10" height="7" fill="#fff"/><path d="M2 3.5 L7 8 L12 3.5" stroke="#062f86" stroke-width="1.2" fill="none"/></svg>
      </span>
      <span class="icon-row__badge" aria-label="website">
        <svg width="14" height="14" viewBox="0 0 14 14"><circle cx="7" cy="7" r="4.5" fill="none" stroke="#fff" stroke-width="1.4"/><path d="M7 2.5 V11.5 M2.5 7 H11.5" stroke="#fff" stroke-width="1"/></svg>
      </span>
      <span class="icon-row__rule"></span>
    </div>
    <div class="contact">
      <p>044-123 456 789</p>
      <p>info@webname.com</p>
      <p>www.websitename.com</p>
    </div>
    <div class="divider"></div>
    <div class="address">
      <p>12345, Address Goes Here</p>
      <p>Country Name, 123456</p>
    </div>
  </section>

  <section class="card card--back">
    <div class="wordmark"><span>k7advisory</span><span class="wordmark__dot"></span></div>
    <p class="web">www.websitename.com</p>
  </section>
</main>
</body>
</html>
```